NEW Modern Sleek Business Card for VR Language Startup

Our startup is using VR to lead the next wave of world language education. We need a two-sided business card that introduces the larger organization (Brightloom Language Inc) and our contact info on one side and shows the product, Glimwoorld, on the other side.

Side 1 (contact info)= Brightloom Logo and Contact info (name, title, phone, email)

Side 2 (product)= Glimworld logo, text, and website
Text= Culturally Immersive Language Learning Games
Website= www.glimworld-play.com

Target Market(s)

Education, Technology

Contact Information for Business Card

Contact info will be updated upon approval of the design. For now, put this as a placeholder.

Perry Dunmore
Founder & CEO
pdunmore@quillpost-mail.net
(555)-014-2286

Font styles to use
Other font styles liked:
• Gibson and Century Gothic are the brand fonts

Requirements
Nice to have
• I would love to see cohesion between the design and colors of the two logos. I have attached a few business card designs that I like, so you can get a feel for my preferred style.

```html
<!DOCTYPE html>
<html lang="en">
<head>
<meta charset="utf-8">
<title>Glimworld / Brightloom Language – Business Card</title>
<link href="https://fonts.googleapis.com/css2?family=Montserrat:wght@400;500;600;700&family=Questrial&display=swap" rel="stylesheet">
<style>
  :root {
    --backdrop: #16171a;
    --card: #222427;
    --card-edge: #2b2d31;
    --ink: #f2f3f5;
    --ink-soft: #c9cbd0;
    --sky: #3fb8e6;
    --violet: #8a4fd8;
    --magenta: #e0398e;
    --orange: #f7893a;
  }
  * { box-sizing: border-box; margin: 0; padding: 0; }
  html, body { width: 1200px; height: 800px; overflow: hidden; }
  body {
    background: var(--backdrop);
    display: flex;
    align-items: center;
    justify-content: center;
    gap: 48px;
    font-family: "Montserrat", "Century Gothic", sans-serif;
    color: var(--ink);
  }
  .card {
    position: relative;
    width: 540px;
    height: 309px;
    background: var(--card);
    border-radius: 18px;
    box-shadow: 0 20px 40px rgba(0,0,0,.45), inset 0 0 0 1px var(--card-edge);
    overflow: hidden;
  }

  /* Product side */
  .product {
    display: flex;
    flex-direction: column;
    align-items: center;
    justify-content: center;
    text-align: center;
  }
  .product .brand {
    display: flex;
    align-items: center;
    gap: 14px;
    margin-bottom: 22px;
  }
  .brand-dot {
    width: 34px; height: 34px;
    border-radius: 50%;
    background: var(--sky);
  }
  .product .brand-name {
    font-size: 46px;
    font-weight: 700;
    color: var(--sky);
    letter-spacing: -0.5px;
  }
  .product .tagline {
    font-family: "Questrial", "Century Gothic", sans-serif;
    font-size: 15px;
    letter-spacing: 1.2px;
    text-transform: uppercase;
    color: var(--ink);
    margin-bottom: 12px;
  }
  .product .website {
    font-size: 14px;
    font-weight: 500;
    color: var(--ink);
  }

  /* Contact side */
  .contact { display: flex; }
  .contact .brand-block {
    width: 52%;
    display: flex;
    flex-direction: column;
    align-items: center;
    justify-content: center;
    gap: 16px;
  }
  .contact .brand-dot {
    width: 40px; height: 40px;
    background: var(--magenta);
  }
  .contact .brand-name {
    font-size: 26px;
    font-weight: 700;
    letter-spacing: 1.5px;
    text-transform: uppercase;
    color: var(--ink);
    text-align: center;
    line-height: 1.15;
  }
  .divider {
    width: 2px;
    margin: 46px 0;
    background: linear-gradient(to bottom, transparent, var(--orange), var(--magenta), var(--violet), var(--sky), transparent);
  }
  .contact .details {
    flex: 1;
    padding: 0 24px;
    display: flex;
    flex-direction: column;
    justify-content: center;
  }
  .person-name {
    font-size: 19px;
    font-weight: 700;
    text-transform: uppercase;
    letter-spacing: .5px;
  }
  .person-title {
    font-size: 14px;
    font-weight: 500;
    margin-top: 2px;
    margin-bottom: 26px;
    background: linear-gradient(90deg, var(--orange), var(--magenta), var(--violet));
    -webkit-background-clip: text;
    background-clip: text;
    color: transparent;
  }
  .contact-list { list-style: none; display: flex; flex-direction: column; gap: 11px; }
  .contact-list li {
    display: flex;
    align-items: center;
    gap: 10px;
    font-size: 12px;
    color: var(--ink-soft);
    white-space: nowrap;
  }
  .contact-icon {
    width: 20px; height: 20px;
    flex: none;
    border-radius: 50%;
    background: linear-gradient(135deg, var(--orange), var(--magenta) 55%, var(--violet));
    display: flex; align-items: center; justify-content: center;
  }
  .contact-icon svg { width: 11px; height: 11px; }
</style>
</head>
<body>

  <section class="card product" aria-label="Product side">
    <div class="brand">
      <span class="brand-dot"></span>
      <span class="brand-name">Glimworld</span>
    </div>
    <p class="tagline">Culturally Immersive Language Learning Games</p>
    <p class="website">www.glimworld-play.com</p>
  </section>

  <section class="card contact" aria-label="Contact side">
    <div class="brand-block">
      <span class="brand-dot"></span>
      <span class="brand-name">Brightloom<br>Language</span>
    </div>
    <div class="divider"></div>
    <div class="details">
      <p class="person-name">Perry Dunmore</p>
      <p class="person-title">Founder &amp; CEO</p>
      <ul class="contact-list">
        <li>
          <span class="contact-icon">
            <svg viewBox="0 0 24 24" fill="#fff"><path d="M6.6 10.8a15.1 15.1 0 0 0 6.6 6.6l2.2-2.2a1 1 0 0 1 1-.25 11.4 11.4 0 0 0 3.6.57 1 1 0 0 1 1 1V20a1 1 0 0 1-1 1A17 17 0 0 1 3 4a1 1 0 0 1 1-1h3.5a1 1 0 0 1 1 1c0 1.25.2 2.45.57 3.57a1 1 0 0 1-.25 1z"/></svg>
          </span>
          (555)-014-2286
        </li>
        <li>
          <span class="contact-icon">
            <svg viewBox="0 0 24 24" fill="none" stroke="#fff" stroke-width="2.4"><rect x="3" y="5" width="18" height="14" rx="1"/><path d="M3 6l9 7 9-7"/></svg>
          </span>
          pdunmore@quillpost-mail.net
        </li>
        <li>
          <span class="contact-icon">
            <svg viewBox="0 0 24 24" fill="none" stroke="#fff" stroke-width="2.2"><circle cx="12" cy="12" r="9"/><path d="M3 12h18M12 3c3 3.2 3 14.8 0 18M12 3c-3 3.2-3 14.8 0 18"/></svg>
          </span>
          www.glimworld-play.com
        </li>
      </ul>
    </div>
  </section>

</body>
</html>
```